New Bicycle shop business card

Hi!
I'm looking for a business card for my new proffesional bike mechanics shop. This shop is only for fixing broken bikes and not selling bikes.
Peferbly a modern and sleek and modern design.
Colors: black, grey, red, white
Information:
Name: Rijwielwerkplaats Vanhoutte
Shop owner: Bart Vanhoutte & Marieke Segers
Website: www.rijwielwerkplaats-vanhoutte.be
Email: info@rijwielwerkplaats-vanhoutte.be
Phone number: +32471902368
Street adres: Kerkweg 46
9940 Bellebeke
Slogan/shop information: Herstellingen van alle merken.
Logo: see files.
Target Market(s)
People who seek a mechanic to fix or upgrade their bikes.
Contact Information for Business Card
Information:
Website: info@rijwielwerkplaats-vanhoutte.be
9940 Bellebeke
Logo: see files.

```html
<!DOCTYPE html>
<html lang="nl">
<head>
<meta charset="utf-8">
<title>Rijwielwerkplaats Vanhoutte – visitekaartje</title>
<link href="https://fonts.googleapis.com/css2?family=Montserrat:wght@700&family=Questrial&display=swap" rel="stylesheet">
<style>
  :root {
    --page: #d9d6d2;
    --card: #111217;
    --card-edge: #1a1b21;
    --white: #ffffff;
    --red: #e0203a;
    --grey: #b9bbc2;
  }
  * { box-sizing: border-box; margin: 0; padding: 0; }
  html, body { width: 1200px; height: 880px; overflow: hidden; }
  body {
    background: var(--page);
    position: relative;
    font-family: "Questrial", "Century Gothic", sans-serif;
    color: var(--white);
  }
  .card {
    position: absolute;
    width: 620px;
    height: 354px;
    border-radius: 22px;
    background: var(--card);
    box-shadow: 0 18px 40px rgba(0,0,0,.35);
    overflow: hidden;
  }
  .card--front { left: 90px; top: 90px; background: linear-gradient(160deg, var(--card-edge), var(--card)); }
  .card--back { left: 490px; top: 436px; }

  .wordmark {
    display: flex;
    align-items: center;
    gap: 12px;
    font-family: "Montserrat", sans-serif;
    font-weight: 700;
    text-transform: uppercase;
    color: var(--white);
    letter-spacing: 1px;
  }
  .wordmark__dot { width: 14px; height: 14px; background: var(--red); flex: none; }

  .card--front .front-content {
    position: absolute; inset: 0;
    display: flex; flex-direction: column; align-items: center; justify-content: center;
    gap: 18px;
  }
  .card--front .wordmark { font-size: 24px; }
  .slogan { font-size: 19px; letter-spacing: .5px; }

  .back-brand {
    position: absolute; left: 0; top: 0; width: 300px; height: 100%;
    display: flex; align-items: center; justify-content: center;
  }
  .back-brand .wordmark { font-size: 15px; flex-direction: column; gap: 10px; text-align: center; line-height: 1.25; }
  .divider {
    position: absolute; left: 312px; top: 70px; width: 1.5px; height: 214px; background: var(--red);
  }
  .contact {
    position: absolute; left: 338px; top: 78px; right: 20px;
    font-size: 13.5px; line-height: 1.55;
  }
  .contact__names {
    font-size: 14.5px; text-transform: uppercase; letter-spacing: .2px;
    padding-bottom: 6px; border-bottom: 1.5px solid var(--red); margin-bottom: 10px;
  }
  .contact__address { margin-bottom: 8px; }
  .contact__row { display: flex; align-items: center; gap: 8px; white-space: nowrap; }
  .contact__row svg { width: 13px; height: 13px; flex: none; fill: var(--red); }
  .contact__web-domain { color: var(--red); }
</style>
</head>
<body>

<section class="card card--front" aria-label="Voorkant visitekaartje">
  <div class="front-content">
    <div class="wordmark"><span class="wordmark__dot"></span>Rijwielwerkplaats Vanhoutte</div>
    <p class="slogan">Herstellingen van alle merken</p>
  </div>
</section>

<section class="card card--back" aria-label="Achterkant visitekaartje">
  <div class="back-brand">
    <div class="wordmark"><span class="wordmark__dot"></span>Rijwielwerkplaats<br>Vanhoutte</div>
  </div>
  <div class="divider"></div>
  <div class="contact">
    <p class="contact__names">Bart Vanhoutte &amp; Marieke Segers</p>
    <p class="contact__address">Kerkweg 46<br>9940 Bellebeke</p>
    <p class="contact__row">
      <svg viewBox="0 0 24 24" aria-hidden="true"><path d="M6.6 10.8a15.1 15.1 0 0 0 6.6 6.6l2.2-2.2a1 1 0 0 1 1-.25 11.4 11.4 0 0 0 3.6.6 1 1 0 0 1 1 1V20a1 1 0 0 1-1 1A17 17 0 0 1 3 4a1 1 0 0 1 1-1h3.5a1 1 0 0 1 1 1c0 1.25.2 2.45.6 3.6a1 1 0 0 1-.25 1z"/></svg>
      +32471902368
    </p>
    <p class="contact__row">
      <svg viewBox="0 0 24 24" aria-hidden="true"><path d="M2 5h20v14H2z M2 5l10 8 10-8" fill="none" stroke="#e0203a" stroke-width="2.4"/></svg>
      info@rijwielwerkplaats-vanhoutte.be
    </p>
    <p class="contact__row">
      <svg viewBox="0 0 24 24" aria-hidden="true"><circle cx="12" cy="12" r="9.5" fill="none" stroke="#e0203a" stroke-width="2"/><path d="M2.5 12h19M12 2.5c3 3 3 16 0 19M12 2.5c-3 3-3 16 0 19" fill="none" stroke="#e0203a" stroke-width="1.6"/></svg>
      <span>www.<span class="contact__web-domain">rijwielwerkplaats-vanhoutte</span>.be</span>
    </p>
  </div>
</section>

</body>
</html>
```